Business card design needed

Card needs to say

Maren Heathwold
Investor - Solutions - Development

My business is in property deals. I would like the words above to be on the card. I have attached a logo for you to copy/recreate.
On the back you could list the following:

Creative property solutions

Thankyou, Maren

Target Market(s)

people wanting to get into the property market, desperate sellers, Mums & Dads wanting to help their kids to purchase a property. People who want to create wealth. People who are stuck and need a solution.

Industry/Entity Type

Business

Contact Information for Business Card

T: 0431 274 506
F: (07) 3842 1739
E: maren47@vbx-mail.com.au

Requirements
Must have
• Simple and effective.
Look like I am here to help
Should not have
• Should not look like a realestate agent

```html
<!DOCTYPE html>
<html lang="en">
<head>
<meta charset="utf-8">
<title>Maren Heathwold – Business Card</title>
<link href="https://fonts.googleapis.com/css2?family=Arimo:wght@400;700&display=swap" rel="stylesheet">
<style>
  :root {
    --backdrop: #3b3b3b;
    --card: #ececec;
    --green: #7fbf45;
    --grey: #767676;
    --faint: #e0e0e0;
  }
  * { margin: 0; padding: 0; box-sizing: border-box; }
  html, body {
    width: 1200px; height: 900px; overflow: hidden;
    background: var(--backdrop);
    font-family: "Arimo", Arial, sans-serif;
  }
  .stage { position: relative; width: 1200px; height: 900px; }
  .card {
    position: absolute; top: 300px;
    width: 525px; height: 296px;
    background: var(--card);
    overflow: hidden;
  }
  .card--front { left: 58px; }
  .card--back { left: 617px; }

  .brand-mark {
    display: flex; align-items: center; gap: 6px;
    color: var(--grey); font-weight: 700;
  }
  .brand-mark__square { width: 12px; height: 12px; background: var(--green); }

  /* front */
  .front-block {
    position: absolute; left: 0; right: 0; top: 104px;
    display: flex; flex-direction: column; align-items: center;
  }
  .front-block .brand-mark { font-size: 15px; margin-bottom: 14px; }
  .front-name {
    color: var(--green); font-weight: 700; font-size: 31px;
    letter-spacing: -0.3px; line-height: 1;
  }
  .front-tagline {
    color: var(--grey); font-weight: 700; font-size: 11px; margin-top: 5px;
  }

  /* back */
  .back-watermark {
    position: absolute; left: -40px; top: 120px;
    font-size: 150px; font-weight: 700; color: var(--faint);
    line-height: 1; white-space: nowrap; letter-spacing: -4px;
  }
  .back-block {
    position: absolute; right: 38px; top: 118px;
    display: flex; flex-direction: column; align-items: flex-end;
  }
  .back-block .brand-mark { font-size: 13px; margin-bottom: 14px; }
  .back-name {
    color: var(--green); font-weight: 700; font-size: 25px;
    letter-spacing: -0.2px; line-height: 1;
  }
  .back-tagline {
    color: var(--grey); font-weight: 700; font-size: 12.5px; margin-top: 2px;
  }
  .contact {
    margin-top: 20px; text-align: right;
    color: var(--grey); font-weight: 700; font-size: 12.5px; line-height: 15px;
  }
  .contact__label { color: var(--green); }
</style>
</head>
<body>
<main class="stage">
  <section class="card card--front" aria-label="Card front">
    <div class="front-block">
      <div class="brand-mark"><span class="brand-mark__square"></span>Heathwold</div>
      <h1 class="front-name">Maren Heathwold</h1>
      <p class="front-tagline">Investor - Solutions - Development</p>
    </div>
  </section>

  <section class="card card--back" aria-label="Card back">
    <div class="back-watermark" aria-hidden="true">Heathwold</div>
    <div class="back-block">
      <div class="brand-mark"><span class="brand-mark__square"></span>Heathwold</div>
      <h2 class="back-name">Maren Heathwold</h2>
      <p class="back-tagline">Creative property solutions</p>
      <p class="contact">
        <span class="contact__label">T:</span> 0431 274 506 <span class="contact__label">F:</span> (07) 3842 1739<br>
        <span class="contact__label">E:</span> maren47@vbx-mail.com.au
      </p>
    </div>
  </section>
</main>
</body>
</html>
```